We (R. T. Galvin & Partners, Inc.) are an executive Search firm based in Los Angeles that is exclusively focused in the Med Tech and Health Tech arenas.   I need a logo to communicate that we are a high end search firm, but also that we are focused in the medicine and science arenas called health tech and med tech.  Many of our clients have robotics and artificial intelligence type products, so it is very technology forward.  I tend to gravitate towards clean, sharp aesthetic as opposed to something that is really over the top.
Attached are files with my logo in two different layouts.  In addition to the letterhead and envelope, I also will need an electronic letterhead in Microsoft Word.  I tend to
I look forward to seeing the designs and just let me know if you have any questions.
Dale

```html
<!DOCTYPE html>
<html lang="en">
<head>
<meta charset="utf-8">
<title>R. T. Galvin &amp; Partners, Inc. — Business Card</title>
<link href="https://fonts.googleapis.com/css2?family=Montserrat:wght@500;600&family=Roboto:wght@400;500&display=swap" rel="stylesheet">
<style>
  :root {
    --bg: #1c1c1d;
    --card: #262627;
    --card-edge: #2e2e2f;
    --accent: #4aa3e0;
    --text: #ffffff;
    --muted: #e6e6e6;
  }
  * { margin: 0; padding: 0; box-sizing: border-box; }
  html, body { width: 1200px; height: 900px; overflow: hidden; }
  body {
    background: radial-gradient(ellipse at 60% 40%, #2a2a2b 0%, var(--bg) 70%);
    font-family: "Roboto", Arial, sans-serif;
    position: relative;
  }
  .card {
    position: absolute;
    left: 250px;
    width: 700px;
    height: 400px;
    background: linear-gradient(135deg, var(--card) 0%, var(--card-edge) 60%, #232324 100%);
    box-shadow: 0 12px 30px rgba(0,0,0,.55);
  }
  .card--front { top: 30px; }
  .card--back { top: 470px; }

  /* brand lockup */
  .brand { font-family: "Montserrat", Arial, sans-serif; font-weight: 500; color: var(--text); text-transform: uppercase; }
  .brand__dot { display: block; border-radius: 50%; background: var(--accent); }
  .brand__name { display: block; letter-spacing: .02em; line-height: 1; }
  .brand__sub { display: block; letter-spacing: .32em; line-height: 1; }

  .card--front .brand {
    position: absolute; left: 0; right: 0; top: 92px;
    display: flex; flex-direction: column; align-items: center;
  }
  .card--front .brand__dot { width: 54px; height: 54px; margin-bottom: 42px; }
  .card--front .brand__name { font-size: 50px; }
  .card--front .brand__sub { font-size: 20px; margin-top: 12px; }

  .card--back .brand {
    position: absolute; left: 58px; top: 158px;
    display: flex; align-items: center; gap: 22px;
  }
  .card--back .brand__dot { width: 46px; height: 46px; flex: none; }
  .card--back .brand__name { font-size: 30px; }
  .card--back .brand__sub { font-size: 12px; margin-top: 7px; letter-spacing: .3em; }

  .divider {
    position: absolute; left: 372px; top: 78px;
    width: 2px; height: 228px; background: var(--accent);
  }

  .contact { position: absolute; left: 396px; top: 82px; color: var(--muted); }
  .contact__name {
    font-family: "Montserrat", Arial, sans-serif; font-weight: 600;
    color: var(--accent); font-size: 31px; letter-spacing: .06em; text-transform: uppercase; line-height: 1;
  }
  .contact__role { font-size: 17px; color: var(--text); margin-top: 4px; }
  .contact__address { font-size: 17px; line-height: 1.3; margin-top: 14px; }
  .contact__list { list-style: none; margin-top: 6px; }
  .contact__item { display: flex; align-items: center; gap: 8px; font-size: 17px; line-height: 1.4; }
  .contact__icon { width: 14px; height: 14px; flex: none; }
</style>
</head>
<body>

<section class="card card--front" aria-label="Card front">
  <div class="brand">
    <span class="brand__dot"></span>
    <span class="brand__name">R. T. Galvin</span>
    <span class="brand__sub">&amp; Partners Inc.</span>
  </div>
</section>

<section class="card card--back" aria-label="Card back">
  <div class="brand">
    <span class="brand__dot"></span>
    <div>
      <span class="brand__name">R. T. Galvin</span>
      <span class="brand__sub">&amp; Partners Inc.</span>
    </div>
  </div>

  <div class="divider"></div>

  <div class="contact">
    <p class="contact__name">Daniel Reyes</p>
    <p class="contact__role">Director</p>
    <p class="contact__address">418 Crestview Road<br>Pasadena, CA 91101</p>
    <ul class="contact__list">
      <li class="contact__item">
        <svg class="contact__icon" viewBox="0 0 24 24" aria-hidden="true"><path fill="#4aa3e0" d="M6.6 10.8a15.1 15.1 0 0 0 6.6 6.6l2.2-2.2a1 1 0 0 1 1-.25 11.4 11.4 0 0 0 3.6.57 1 1 0 0 1 1 1V20a1 1 0 0 1-1 1A17 17 0 0 1 3 4a1 1 0 0 1 1-1h3.5a1 1 0 0 1 1 1c0 1.25.2 2.45.57 3.57a1 1 0 0 1-.25 1z"/></svg>
        +1(626)555-01 48372
      </li>
      <li class="contact__item">
        <svg class="contact__icon" viewBox="0 0 24 24" aria-hidden="true"><path fill="#4aa3e0" d="M6 2h12v5H6zM3 8h18a1 1 0 0 1 1 1v8h-4v5H6v-5H2V9a1 1 0 0 1 1-1zm5 8v4h8v-4z"/></svg>
        +1(0)626-5550193
      </li>
      <li class="contact__item">
        <svg class="contact__icon" viewBox="0 0 24 24" aria-hidden="true"><rect x="2.5" y="5" width="19" height="14" fill="none" stroke="#4aa3e0" stroke-width="2"/><path d="M3 6l9 7 9-7" fill="none" stroke="#4aa3e0" stroke-width="2"/></svg>
        R. T. Galvin@Partners, Inc.com
      </li>
      <li class="contact__item">
        <svg class="contact__icon" viewBox="0 0 24 24" aria-hidden="true"><g fill="none" stroke="#4aa3e0" stroke-width="1.8"><circle cx="12" cy="12" r="9.5"/><ellipse cx="12" cy="12" rx="4" ry="9.5"/><path d="M2.5 12h19M4 7h16M4 17h16"/></g></svg>
        R. T. Galvin &amp; Partners, Inc.com
      </li>
    </ul>
  </div>
</section>

</body>
</html>
```